Danielle Voskuijl Photography
Letterhead & Business Card Design
Danielle Voskuijl Photography - Photography
Creative Brief
Professional
Danielle Voskuijl
Photographer / Owner
418 Bramblecrest Lane Fort McMurray, AB T9K 2P7
daniellevoskuijlphotography@quillmarrow.example
www.daniellevoskuijlphotography.example
I think I'd like to include a photo I've taken...thoughts?

```html
<!DOCTYPE html>
<html lang="en">
<head>
<meta charset="utf-8">
<title>Danielle Voskuijl Photography – Stationery</title>
<link rel="stylesheet" href="https://fonts.googleapis.com/css2?family=Raleway:wght@300;400&display=swap">
<style>
  :root {
    --backdrop: #e9e6e1;
    --paper: #ffffff;
    --paper-edge: #d9d6d1;
    --teal: #4aaab8;
    --ink: #6f6259;
    --ink-soft: #9a8f87;
    --flap-line: #cfcbc6;
  }
  * { box-sizing: border-box; margin: 0; padding: 0; }
  html, body { width: 1200px; height: 847px; overflow: hidden; }
  body {
    background: var(--backdrop);
    font-family: "Raleway", sans-serif;
    color: var(--ink);
    position: relative;
  }
  .sheet {
    position: absolute;
    background: var(--paper);
    border: 1px solid var(--paper-edge);
    box-shadow: 0 2px 6px rgba(0,0,0,0.12);
    overflow: hidden;
  }
  .sheet-under { transform: rotate(-2deg); }

  /* Logotype: one font, one weight, one colour */
  .brand { display: flex; align-items: center; gap: 8px; }
  .brand-dot { border-radius: 50%; background: var(--teal); flex: none; }
  .brand-text { display: flex; flex-direction: column; font-weight: 300; color: var(--teal); line-height: 1.1; white-space: nowrap; }
  .brand-name { letter-spacing: 0.02em; }
  .brand-tag { font-size: 0.5em; letter-spacing: 0.42em; margin-top: 2px; }

  .contact { font-weight: 400; color: var(--ink-soft); line-height: 1.55; white-space: nowrap; }

  /* Letterhead */
  .letterhead { left: 92px; top: 100px; width: 440px; height: 580px; }
  .letterhead-under { left: 104px; top: 106px; width: 440px; height: 580px; }
  .letterhead .brand { position: absolute; left: 30px; top: 26px; }
  .letterhead .brand-dot { width: 40px; height: 40px; }
  .letterhead .brand-text { font-size: 17px; }
  .letterhead .contact { position: absolute; left: 32px; top: 76px; font-size: 6.5px; }

  /* Envelope back */
  .envelope-back { left: 590px; top: 100px; width: 440px; height: 180px; }
  .envelope-back svg { position: absolute; inset: 0; }
  .envelope-back .seal { position: absolute; left: 204px; top: 52px; width: 32px; height: 32px; border-radius: 50%; background: var(--teal); }

  /* Envelope front */
  .envelope-front { left: 700px; top: 300px; width: 440px; height: 190px; }
  .envelope-front .brand { position: absolute; left: 18px; top: 18px; }
  .envelope-front .brand-dot { width: 30px; height: 30px; }
  .envelope-front .brand-text { font-size: 13px; }
  .envelope-front .contact { position: absolute; left: 20px; top: 58px; font-size: 6px; }

  /* Business cards */
  .card { top: 560px; width: 290px; height: 170px; border-radius: 8px; }
  .card-front { left: 515px; }
  .card-front .brand { position: absolute; left: 16px; top: 16px; }
  .card-front .brand-dot { width: 32px; height: 32px; }
  .card-front .brand-text { font-size: 14px; }
  .card-front .person { position: absolute; left: 16px; top: 64px; font-size: 7px; line-height: 1.45; color: var(--ink-soft); }
  .card-front .person strong { font-weight: 400; color: var(--ink); }
  .card-front .contact { position: absolute; left: 16px; top: 92px; font-size: 5.5px; }
  .card-front .website { position: absolute; left: 16px; bottom: 12px; font-size: 5.5px; color: var(--ink-soft); }
  .card-back { left: 835px; }
  .card-back .brand { position: absolute; left: 20px; top: 52px; gap: 10px; }
  .card-back .brand-dot { width: 44px; height: 44px; }
  .card-back .brand-text { font-size: 18px; }
  .card-back .website { position: absolute; right: 18px; bottom: 14px; font-size: 6.5px; color: var(--ink-soft); }
</style>
</head>
<body>

<div class="sheet letterhead-under sheet-under" aria-hidden="true"></div>
<section class="sheet letterhead" aria-label="Letterhead">
  <div class="brand"><span class="brand-dot"></span><span class="brand-text"><span class="brand-name">Danielle Voskuijl</span><span class="brand-tag">PHOTOGRAPHY</span></span></div>
  <p class="contact">418 Bramblecrest Lane Fort McMurray, AB T9K 2P7<br>Phone 780.555.0147<br>daniellevoskuijlphotography@quillmarrow.example</p>
</section>

<section class="sheet envelope-back" aria-label="Envelope back">
  <svg width="440" height="180" viewBox="0 0 440 180">
    <polyline points="0,0 220,70 440,0" fill="none" stroke="var(--flap-line)" stroke-width="1.2"/>
    <polyline points="0,180 175,95 265,95 440,180" fill="none" stroke="var(--flap-line)" stroke-width="1"/>
  </svg>
  <span class="seal"></span>
</section>

<section class="sheet envelope-front" aria-label="Envelope front">
  <div class="brand"><span class="brand-dot"></span><span class="brand-text"><span class="brand-name">Danielle Voskuijl</span><span class="brand-tag">PHOTOGRAPHY</span></span></div>
  <p class="contact">418 Bramblecrest Lane<br>Fort McMurray, AB T9K 2P7</p>
</section>

<section class="sheet card card-front" aria-label="Business card front">
  <div class="brand"><span class="brand-dot"></span><span class="brand-text"><span class="brand-name">Danielle Voskuijl</span><span class="brand-tag">PHOTOGRAPHY</span></span></div>
  <p class="person"><strong>Danielle Voskuijl</strong><br>Photographer / Owner</p>
  <p class="contact">418 Bramblecrest Lane<br>Fort McMurray, AB T9K 2P7<br>Phone 780.555.0147<br>daniellevoskuijlphotography@quillmarrow.example</p>
  <p class="website">www.daniellevoskuijlphotography.example</p>
</section>

<section class="sheet card card-back" aria-label="Business card back">
  <div class="brand"><span class="brand-dot"></span><span class="brand-text"><span class="brand-name">Danielle Voskuijl</span><span class="brand-tag">PHOTOGRAPHY</span></span></div>
  <p class="website">www.daniellevoskuijlphotography.example</p>
</section>

</body>
</html>
```